KORV PTY LTD - Business Cards

Design a modern business card - using the attached Designs.
Same design as on the front, apart from the names/numbers/emails to be different.
We want the cards to be very glossy to stand out, do I think the simple black/white/metallic will be effective.
Both lots of details below:

Tom Wrenshaw
Director
tom_korv@nulvane.com
0438 274 093

Lewis Corbyn
Director
lewis_korv@nulvane.com
0419 385 642

Industry/Entity Type

Business

```html
<!DOCTYPE html>
<html lang="en">
<head>
<meta charset="utf-8">
<title>KORV PTY LTD – Business Cards</title>
<link rel="stylesheet" href="https://fonts.googleapis.com/css2?family=Bitter:wght@400;700&family=Open+Sans:wght@400&display=swap">
<style>
  :root {
    --page-bg: #e9e7e4;
    --metal-light: #e4e6e6;
    --metal-mid: #c9cccd;
    --metal-dark: #aeb2b4;
    --back-grey: #b4b4b4;
    --ink: #1f1f1f;
    --ink-soft: #3a3a3a;
    --divider: #9a9c9e;
    --mark: #2b2b2b;
  }
  * { margin: 0; padding: 0; box-sizing: border-box; }
  html, body {
    width: 1200px;
    height: 465px;
    overflow: hidden;
    background: var(--page-bg);
  }
  .sheet {
    position: relative;
    width: 1200px;
    height: 465px;
    display: flex;
    justify-content: center;
    align-items: center;
    gap: 40px;
  }
  .card {
    position: relative;
    width: 540px;
    height: 310px;
    box-shadow: 0 6px 18px rgba(0,0,0,0.25);
  }
  .card--front {
    background:
      repeating-linear-gradient(0deg, rgba(255,255,255,0.10) 0 1px, rgba(0,0,0,0.03) 1px 3px),
      linear-gradient(160deg, var(--metal-light) 0%, var(--metal-mid) 55%, var(--metal-dark) 100%);
  }
  .card--back {
    background: var(--back-grey);
    display: flex;
    justify-content: center;
    align-items: center;
  }
  .brand {
    display: flex;
    align-items: center;
    gap: 10px;
    font-family: 'Bitter', serif;
    font-weight: 700;
    color: var(--mark);
    white-space: nowrap;
  }
  .brand__dot {
    border-radius: 50%;
    background: var(--mark);
    flex: none;
  }
  .card--front .brand {
    position: absolute;
    left: 44px;
    top: 50%;
    transform: translateY(-50%);
    font-size: 26px;
  }
  .card--front .brand__dot { width: 22px; height: 22px; }
  .card--back .brand { font-size: 44px; gap: 16px; }
  .card--back .brand__dot { width: 36px; height: 36px; }
  .divider {
    position: absolute;
    left: 262px;
    top: 100px;
    width: 1px;
    height: 150px;
    background: var(--divider);
  }
  .details {
    position: absolute;
    left: 292px;
    top: 98px;
    color: var(--ink);
  }
  .details__name {
    font-family: 'Bitter', serif;
    font-weight: 400;
    font-size: 22px;
    line-height: 1.2;
  }
  .details__role {
    font-family: 'Bitter', serif;
    font-size: 14px;
    color: var(--ink-soft);
    margin-top: 4px;
  }
  .contact {
    list-style: none;
    margin-top: 26px;
    font-family: 'Open Sans', sans-serif;
    font-size: 15px;
    color: var(--ink);
  }
  .contact__item {
    display: flex;
    align-items: center;
    gap: 6px;
    line-height: 1.5;
  }
  .contact__icon { width: 12px; height: 12px; flex: none; }
</style>
</head>
<body>
  <main class="sheet">
    <section class="card card--front" aria-label="Business card front">
      <div class="brand"><span class="brand__dot"></span>KORV PTY LTD</div>
      <div class="divider"></div>
      <div class="details">
        <h1 class="details__name">Lewis Corbyn</h1>
        <p class="details__role">Director</p>
        <ul class="contact">
          <li class="contact__item">
            <svg class="contact__icon" viewBox="0 0 12 12" aria-hidden="true">
              <circle cx="6" cy="6" r="5.3" fill="none" stroke="#1f1f1f" stroke-width="1"/>
              <path d="M4 3.2 L5 3 L5.6 4.6 L4.9 5.1 Q5.5 6.6 6.9 7.2 L7.4 6.5 L9 7.1 L8.8 8.1 Q6 8.6 3.9 5.9 Q3.5 4.3 4 3.2Z" fill="#1f1f1f"/>
            </svg>
            <span>0419 385 642</span>
          </li>
          <li class="contact__item">
            <svg class="contact__icon" viewBox="0 0 12 12" aria-hidden="true">
              <path d="M1 5 L6 1.5 L11 5 V10.5 H1Z" fill="#1f1f1f"/>
              <path d="M1.5 5.2 L6 8.2 L10.5 5.2" fill="none" stroke="#c9cccd" stroke-width="1"/>
            </svg>
            <span>lewis_korv@nulvane.com</span>
          </li>
        </ul>
      </div>
    </section>

    <section class="card card--back" aria-label="Business card back">
      <div class="brand"><span class="brand__dot"></span>KORV PTY LTD</div>
    </section>
  </main>
</body>
</html>
```